Anzeigengestaltung für einen einen ambulanten Pflegedienst
Zielgruppe
Insgesamt möchte ich gern drei Anzeigen für das Internet gestalten haben. Ich betreibe einen ambulanten Pflegedienst. Die erste Anzeige soll dazu dienen Kunden anzusprechen, die einen Unterstützungsbedarf und / oder einen Beratungsbedarf haben. Die zweite Anzeige soll dazu dienen neues Personal anzuwerben. Die dritte Anzeige soll speziell potenzielle Azubis ansprechen. Die Anzeigen sind gedacht für Tralvio und Pexumora hauptsächlich. In den Druck sollte es schon 10cm x 8cm sein. Es wäre super wenn vielleicht auch eine Art Aufruf an ehrenamtliche Mitarbeiter erfolgt.
Aufgabenstellung
Die Anzeigen sollen den Stil der Homepage beibehalten. Freundlich, frisch und agil wirken. Alle sollten emotional ansprechend sein und gerade der für zukünftige Mitarbeiter sollte deutlich ein gutes Betriebsklima vermitteln. Als Datei habe ich einige Bilder, die bereits für die Homepage oder Flyer verwendet wurden hochgeladen. des Weiteren habe ich die einzelnen Seiten des Flyers hochgeladen.

```html
<!DOCTYPE html>
<html lang="de">
<head>
<meta charset="utf-8">
<title>Team Verado – Anzeigen</title>
<link rel="stylesheet" href="https://fonts.googleapis.com/css2?family=Anton&family=Red+Hat+Display:wght@400;500;700&display=swap">
<style>
:root{
  --stage:#bdbdbd;
  --sky-top:#cfe4f7;
  --sky-bottom:#f2f7fc;
  --green:#7cb342;
  --teal:#3aa89e;
  --teal-light:#7fd0cb;
  --blue:#2ea3dc;
  --ink:#1c1c1c;
  --grey-text:#5b5b5b;
  --white:#ffffff;
}
*{box-sizing:border-box;margin:0;padding:0}
html,body{width:1200px;height:1117px;overflow:hidden}
body{background:var(--stage);position:relative;font-family:"Red Hat Display",Arial,sans-serif}
.ad-frame{position:absolute;width:544px;height:434px;box-shadow:0 3px 8px rgba(0,0,0,.3);overflow:hidden}
.ad-frame.course{left:611px;top:121px}
.ad-frame.care{left:50px;top:121px}
.ad-frame.jobs{left:328px;top:572px}
.ad{position:absolute;left:0;top:0;width:725px;height:579px;transform:scale(.75);transform-origin:0 0;
  background:linear-gradient(160deg,var(--sky-top),var(--sky-bottom) 60%)}
.ad svg.shapes{position:absolute;left:0;top:0;width:725px;height:579px}
.brand-mark{position:absolute;width:78px;height:78px;border-radius:50%;border:5px solid var(--teal)}
.brand-name{position:absolute;font-size:34px;font-weight:500;color:var(--grey-text);letter-spacing:.5px;white-space:nowrap}
.kicker{position:absolute;color:var(--teal);font-size:20px;line-height:22px}
.headline{position:absolute;font-family:"Anton",Impact,sans-serif;color:var(--ink);text-transform:uppercase;letter-spacing:-.5px}
.body-copy{position:absolute;font-size:12.5px;line-height:15px}
.url-pill{position:absolute;border:2.5px solid var(--white);border-radius:20px;color:var(--white);font-weight:700;
  font-size:17px;display:flex;align-items:center;justify-content:center;width:253px;height:34px}
.requirements{position:absolute;left:46px;top:397px;width:636px;height:100px;border-radius:14px;
  border:4px solid var(--blue);background:rgba(240,247,253,.95);box-shadow:0 0 0 4px var(--white);
  display:flex;align-items:center;padding:0 20px}
.req-col{display:flex;flex-direction:column;gap:9px;padding:0 14px;border-right:1.5px solid var(--grey-text)}
.req-col:last-child{border-right:none}
.req-col span{font-size:15px;color:var(--ink);display:flex;align-items:center;gap:8px;white-space:nowrap}
.req-col svg{width:12px;height:12px}
</style>
</head>
<body>

<!-- Anzeige Kunden -->
<div class="ad-frame care">
 <div class="ad">
  <svg class="shapes" viewBox="0 0 725 579">
   <polygon points="0,385 320,398 420,340 725,290 725,305 420,355 320,413 0,400" fill="var(--teal-light)"/>
   <polygon points="0,405 330,418 425,362 725,310 725,579 0,579" fill="var(--green)"/>
   <polygon points="580,579 725,500 725,579" fill="var(--white)"/>
   <g fill="var(--teal)"><rect x="612" y="30" width="12" height="36"/><rect x="600" y="42" width="36" height="12"/></g>
   <g fill="var(--green)"><rect x="654" y="45" width="6" height="18"/><rect x="648" y="51" width="18" height="6"/>
    <rect x="336" y="72" width="10" height="28"/><rect x="327" y="81" width="28" height="10"/>
    <rect x="362" y="70" width="5" height="14"/><rect x="357" y="75" width="14" height="5"/></g>
   <polygon points="527,30 704,133 704,340 527,445 350,340 350,133" fill="var(--white)" stroke="var(--white)" stroke-width="24" stroke-linejoin="round"/>
   <polygon points="527,38 696,137 696,336 527,437 358,336 358,137" fill="var(--blue)" stroke="var(--blue)" stroke-width="14" stroke-linejoin="round"/>
   <polygon points="527,62 676,149 676,324 527,413 378,324 378,149" fill="url(#photoCare)" stroke="#d7e3ee" stroke-width="6" stroke-linejoin="round" role="img" aria-label="Foto: Arzt im Gespräch mit einer Patientin"/>
   <defs><linearGradient id="photoCare" x1="0" y1="0" x2="1" y2="1"><stop offset="0" stop-color="#e9eef2"/><stop offset=".6" stop-color="#c9d6e0"/><stop offset="1" stop-color="#8fb3cf"/></linearGradient></defs>
  </svg>
  <div class="brand-mark" style="left:126px;top:55px"></div>
  <div class="brand-name" style="left:52px;top:152px">TEAM VERADO</div>
  <div class="kicker" style="left:52px;top:229px">Wir zählen auf Dich</div>
  <div class="headline" style="left:52px;top:258px;font-size:44px;line-height:45px">Was wird auf<br>dich zukommen?</div>
  <div class="body-copy" style="left:40px;top:466px;width:640px;text-align:center;color:var(--white)">Die ambulante Pflege wird in der Häuslichkeit der Patienten durchgeführt. Es ist unser Ziel die Pflege für alle Beteiligten so würdevoll und respektvoll zu gestalten wie möglich. Der zu betreuende Mensch steht dabei im Vordergrund, daher gewähren wir jedem die Zeit, die er braucht.</div>
  <div class="url-pill" style="left:236px;top:523px">www.verado-pflege.de</div>
 </div>
</div>

<!-- Anzeige Pflegekurse -->
<div class="ad-frame course">
 <div class="ad">
  <svg class="shapes" viewBox="0 0 725 579">
   <polygon points="0,450 440,500 725,420 725,435 440,515 0,465" fill="var(--teal-light)"/>
   <polygon points="0,470 440,520 725,440 725,579 0,579" fill="var(--green)"/>
   <polygon points="560,579 725,500 725,579" fill="var(--white)"/>
   <g fill="var(--teal)"><rect x="666" y="22" width="14" height="42"/><rect x="652" y="36" width="42" height="14"/></g>
   <g fill="var(--green)"><rect x="374" y="65" width="12" height="32"/><rect x="364" y="75" width="32" height="12"/>
    <rect x="404" y="58" width="5" height="16"/><rect x="398" y="63" width="17" height="5"/></g>
   <polygon points="535,37 725,147 725,427 535,537 345,427 345,147" fill="var(--white)" stroke="var(--white)" stroke-width="24" stroke-linejoin="round"/>
   <polygon points="535,45 725,153 725,421 535,529 353,421 353,153" fill="var(--blue)" stroke="var(--blue)" stroke-width="14" stroke-linejoin="round"/>
   <polygon points="535,70 725,175 725,400 535,505 375,410 375,165" fill="url(#photoCourse)" stroke="#d7e3ee" stroke-width="6" stroke-linejoin="round" role="img" aria-label="Foto: lächelnder Arzt im weißen Kittel mit Stethoskop"/>
   <defs><linearGradient id="photoCourse" x1="0" y1="0" x2="1" y2="1"><stop offset="0" stop-color="#dfe8ef"/><stop offset=".55" stop-color="#eef2f5"/><stop offset="1" stop-color="#9fb8cc"/></linearGradient></defs>
  </svg>
  <div class="brand-mark" style="left:126px;top:48px"></div>
  <div class="brand-name" style="left:52px;top:154px">TEAM VERADO</div>
  <div class="kicker" style="left:52px;top:224px">Unser Schulungsangebot<br>für Sie</div>
  <div class="headline" style="left:52px;top:266px;font-size:58px;line-height:64px">Pflegekurse</div>
  <div class="body-copy" style="left:54px;top:340px;width:260px;color:var(--ink);font-size:12px;line-height:14.5px">Sie sind pflegende*r Angehörige*r und möchten lernen, besser mit der Erkrankung der/des Pflegebedürftige*n umzugehen und die Pflege allgemein effektiver und belastungsarmer zur gestalten? Dann sind Sie bei uns genau richtig</div>
  <div class="url-pill" style="left:48px;top:526px">www.verado-pflege.de</div>
 </div>
</div>

<!-- Anzeige Stellen -->
<div class="ad-frame jobs">
 <div class="ad">
  <svg class="shapes" viewBox="0 0 725 579">
   <polygon points="0,422 360,410 440,365 725,345 725,360 440,380 360,425 0,437" fill="var(--teal-light)"/>
   <polygon points="0,442 360,430 440,385 725,365 725,579 0,579" fill="var(--green)"/>
   <g fill="var(--teal)"><rect x="624" y="28" width="12" height="34"/><rect x="613" y="39" width="34" height="12"/></g>
   <g fill="var(--green)"><rect x="658" y="50" width="6" height="16"/><rect x="653" y="55" width="16" height="6"/>
    <rect x="340" y="82" width="10" height="28"/><rect x="331" y="91" width="28" height="10"/>
    <rect x="363" y="78" width="5" height="13"/><rect x="359" y="82" width="13" height="5"/></g>
   <g fill="#8fbf55" opacity=".5"><rect x="570" y="510" width="60" height="69"/><rect x="612" y="512" width="10" height="26"/><rect x="604" y="520" width="26" height="10"/><rect x="655" y="536" width="6" height="14"/><rect x="651" y="540" width="14" height="6"/></g>
   <polygon points="538,37 692,127 692,307 538,397 384,307 384,127" fill="var(--white)" stroke="var(--white)" stroke-width="24" stroke-linejoin="round"/>
   <polygon points="538,45 684,131 684,303 538,389 392,303 392,131" fill="var(--blue)" stroke="var(--blue)" stroke-width="14" stroke-linejoin="round"/>
   <polygon points="538,68 664,142 664,292 538,366 412,292 412,142" fill="url(#photoJobs)" stroke="#d7e3ee" stroke-width="6" stroke-linejoin="round" role="img" aria-label="Foto: Pfleger und Ärztin Rücken an Rücken"/>
   <defs><linearGradient id="photoJobs" x1="0" y1="0" x2="1" y2="1"><stop offset="0" stop-color="#f4f6f8"/><stop offset=".6" stop-color="#e3e9ee"/><stop offset="1" stop-color="#b7c9d8"/></linearGradient></defs>
  </svg>
  <div class="brand-mark" style="left:118px;top:52px"></div>
  <div class="brand-name" style="left:52px;top:154px">TEAM VERADO</div>
  <div class="kicker" style="left:52px;top:217px;font-size:22px;line-height:24px">Wir suchen Dich!</div>
  <div class="headline" style="left:52px;top:246px;font-size:62px;line-height:64px">Was bringst<br>du mit?</div>
  <div class="requirements">
   <div class="req-col">
    <span><svg viewBox="0 0 12 12"><path d="M1 6.5 4.5 10 11 2" fill="none" stroke="var(--green)" stroke-width="2.4"/></svg>Teamfähigkeit</span>
    <span><svg viewBox="0 0 12 12"><path d="M1 6.5 4.5 10 11 2" fill="none" stroke="var(--green)" stroke-width="2.4"/></svg>Hilfsbereitschaft</span>
   </div>
   <div class="req-col">
    <span><svg viewBox="0 0 12 12"><path d="M1 6.5 4.5 10 11 2" fill="none" stroke="var(--green)" stroke-width="2.4"/></svg>Engagement</span>
    <span><svg viewBox="0 0 12 12"><path d="M1 6.5 4.5 10 11 2" fill="none" stroke="var(--green)" stroke-width="2.4"/></svg>Führerschein Klasse B</span>
   </div>
   <div class="req-col">
    <span><svg viewBox="0 0 12 12"><path d="M1 6.5 4.5 10 11 2" fill="none" stroke="var(--green)" stroke-width="2.4"/></svg>Gute Deutschkenntnisse</span>
    <span><svg viewBox="0 0 12 12"><path d="M1 6.5 4.5 10 11 2" fill="none" stroke="var(--green)" stroke-width="2.4"/></svg>in Wort und Schrif</span>
   </div>
  </div>
  <div class="url-pill" style="left:232px;top:523px">www.verado-pflege.de</div>
 </div>
</div>

</body>
</html>
```